Homemaking training schools needs a Business Card design

Designer, Hello!

No special requirements, good-looking enough.
--------------------------------------------------------------------------

Name: Marcus Dole
Chairman
Tel: 0574-71948263
Mobile: 13857420916
Email: kelvora@mailnest.example
Web: www.prt2019.example
Add: No.258, LanpingJie, BeiyuanQu, Ningbo, Zhejiang

LOGO
Ningbo PRT Homemaking Training School

Target Market(s)

pregnant women, mothers, infants, the elderly and families, including cleaning, cooking, nursing training.

Industry/Entity Type

Business

Contact Information for Business Card

Name: Marcus Dole
Chairman
Tel: 0574-71948263
Mobile: 13857420916
Email: kelvora@mailnest.example
Web: www.prt2019.example

LOGO

Font styles to use
Serif
Sans Serif
Decorative

Requirements
Nice to have
• Feels: clean, specifications, safety, comfort, warmth and happiness.

```html
<!DOCTYPE html>
<html lang="en">
<head>
<meta charset="utf-8">
<title>PinRuiTang Business Card</title>
<link rel="stylesheet" href="https://fonts.googleapis.com/css2?family=Montserrat:wght@400;500;600;700;800&display=swap">
<style>
  :root {
    --stage: #d9d9d9;
    --charcoal: #3b3b3b;
    --brand-blue: #1676c8;
    --brand-pink: #e5137f;
    --paper: #ffffff;
    --ink: #1c1c1c;
  }
  * { box-sizing: border-box; margin: 0; padding: 0; }
  html, body { width: 1200px; height: 900px; overflow: hidden; }
  body {
    background: var(--stage);
    font-family: "Montserrat", sans-serif;
    position: relative;
  }
  .card {
    position: absolute;
    width: 700px;
    height: 400px;
    overflow: hidden;
    box-shadow: 0 10px 28px rgba(0,0,0,0.25);
  }
  .card-bands { position: absolute; inset: 0; }

  /* Back side */
  .card-back { left: 110px; top: 30px; background: var(--charcoal); }
  .card-back .wordmark {
    position: absolute; left: 0; right: 0; top: 130px;
    display: flex; align-items: center; justify-content: center; gap: 14px;
  }
  .wordmark-dot { width: 18px; height: 18px; border-radius: 50%; background: var(--brand-pink); flex: none; }
  .card-back .wordmark-name {
    font-weight: 700; font-size: 56px; color: var(--paper); letter-spacing: -0.5px;
  }
  .card-back .web {
    position: absolute; left: 28px; bottom: 14px;
    font-weight: 700; font-size: 19px; color: var(--brand-blue);
  }

  /* Front side */
  .card-front { left: 390px; top: 470px; background: var(--paper); }
  .card-front .wordmark {
    position: absolute; left: 36px; top: 50px;
    display: flex; align-items: center; gap: 12px;
  }
  .card-front .wordmark-name {
    font-weight: 700; font-size: 40px; color: var(--brand-blue); letter-spacing: -0.5px;
  }
  .holder { position: absolute; right: 34px; top: 170px; text-align: right; }
  .holder-name { font-weight: 800; font-size: 30px; color: var(--brand-blue); letter-spacing: 0.5px; }
  .holder-role { font-weight: 600; font-size: 12px; color: var(--ink); letter-spacing: 1.5px; margin-top: 2px; }
  .divider {
    position: absolute; left: 34px; right: 34px; top: 246px;
    height: 2px; background: var(--brand-blue);
  }
  .contacts {
    position: absolute; left: 34px; top: 260px;
    list-style: none; display: flex; flex-direction: column; gap: 5px;
  }
  .contacts li {
    display: flex; align-items: center; gap: 10px;
    font-weight: 600; font-size: 16px; color: var(--brand-blue);
  }
  .contacts svg { width: 14px; height: 14px; flex: none; }
  .address {
    position: absolute; right: 26px; top: 318px; text-align: right;
    font-weight: 600; font-size: 14px; line-height: 1.5; color: var(--paper);
    white-space: nowrap;
  }
</style>
</head>
<body>

  <section class="card card-back" aria-label="Business card, back">
    <svg class="card-bands" viewBox="0 0 700 400" preserveAspectRatio="none" aria-hidden="true">
      <polygon points="0,330 300,330 360,355 700,355 700,400 0,400" fill="#ffffff"/>
      <polygon points="330,340 700,250 700,272 372,355" fill="#1676c8"/>
    </svg>
    <div class="wordmark">
      <span class="wordmark-dot"></span>
      <span class="wordmark-name">PinRuiTang</span>
    </div>
    <p class="web">www.prt2019.example</p>
  </section>

  <section class="card card-front" aria-label="Business card, front">
    <svg class="card-bands" viewBox="0 0 700 400" preserveAspectRatio="none" aria-hidden="true">
      <polygon points="0,382 700,382 700,400 0,400" fill="#e5137f"/>
      <polygon points="430,292 700,292 700,400 380,400" fill="#1676c8"/>
    </svg>
    <div class="wordmark">
      <span class="wordmark-dot"></span>
      <span class="wordmark-name">PinRuiTang</span>
    </div>
    <div class="holder">
      <p class="holder-name">MARCUS DOLE</p>
      <p class="holder-role">CHAIRMAN</p>
    </div>
    <div class="divider"></div>
    <ul class="contacts">
      <li>
        <svg viewBox="0 0 16 16" aria-hidden="true"><path d="M3 1.5l3 .5 1 3.5-2 1.2a9 9 0 0 0 4.3 4.3l1.2-2 3.5 1 .5 3c-.2.8-1 1.5-2 1.5C6.7 14.5 1.5 9.3 1.5 3.5c0-1 .7-1.8 1.5-2z" fill="#1c1c1c"/></svg>
        0574-71948263
      </li>
      <li>
        <svg viewBox="0 0 16 16" aria-hidden="true"><rect x="4" y="1" width="8" height="14" rx="1.5" fill="none" stroke="#1c1c1c" stroke-width="1.6"/><circle cx="8" cy="12.3" r="0.9" fill="#1c1c1c"/></svg>
        13857420916
      </li>
      <li>
        <svg viewBox="0 0 16 16" aria-hidden="true"><rect x="1.5" y="3.5" width="13" height="9" fill="none" stroke="#1c1c1c" stroke-width="1.5"/><path d="M1.5 3.5L8 9l6.5-5.5" fill="none" stroke="#1c1c1c" stroke-width="1.5"/></svg>
        kelvora@mailnest.example
      </li>
      <li>
        <svg viewBox="0 0 16 16" aria-hidden="true"><circle cx="8" cy="8" r="6.5" fill="none" stroke="#1c1c1c" stroke-width="1.4"/><ellipse cx="8" cy="8" rx="2.8" ry="6.5" fill="none" stroke="#1c1c1c" stroke-width="1.2"/><path d="M1.5 8h13" stroke="#1c1c1c" stroke-width="1.2"/></svg>
        www.prt2019.example
      </li>
    </ul>
    <p class="address">258, LanpingJie<br>BeiyuanQu, Ningbo, Zhejiang</p>
  </section>

</body>
</html>
```